Property Portal needs Chatterloop Cover Image and Sponsor Ad Design

WHO WE ARE
Hi Pitchers! We are an advertising portal that focus on presenting the latest property launches in Singapore. Our platform and interface will provide consumer an enjoyable and easy browsing experience looking for their ideal property to buy/invest, while ensuring updated information, images/videos, and other useful description is provided on each project.

WHAT WE NEED
Our website is www.brightkeyhomes.sg, and we need designs for our Chatterloop page www.facebook.com/brightkeyhomes. One as the Cover Image (815 x 315), and one as our Sponsor Ad Image (1200 x 627). The 2 designs can be similar or different.

DESIGN
We want to convey a professional and sociable feel. A "cool" and elegant design may be suitable, although feel free to have your own look & feel as long as it suits our purpose. Try to have a focus, and not look messy. We don't want to look cheap, spammy or boring in any sense. Be creative and purposeful =) You may use the snapvault images attached or you can use your own. Add symbols or graphics if it helps to give the design a better feel.

For your reference, I find there is a number of good designs with nice look & feel in this project including those withdraw/eliminated.
http://chatterloop.pitchmart.example/contest.aspx?id=218907&page=2
http://chatterloop.pitchmart.example/contest.aspx?id=218907

IDEAS
You may want to embed our portal in an SLATEX device as part of the design (see samples below but replace callpod with SlateX). And/or you can have a blur-out image background to have a focus on what you want to show. Please note that we are not restricting any other designs concept, this is just an idea I have.

CAPTIONS
You may use one or a few of the sample captions below.
- Singapore Latest Property Launches In One Portal (slight emphasis on "in one portal")
- Latest Projects • Updated Info • Best Pricing
- Residential • Commercial • Overseas (perhaps label on images)

Hope we can find an ideal design here. We will request from pitchmart to increase the project budget to give out more participation payments if there is a few good ones. We are also looking to find suitable designers for our future projects as we need a few more designs. If you have questions, feel free to ask me and I will reply promptly.

Reason: Project cancelled and relaunch with different purpose, moved from Newsletter to Chatterloop Design.

IDEAS (UPDATED) I am thinking one way to showcase our portal is perhaps to have our website embedded in an slatex and/or notebook pro device as part of the design. I've attached some designs I came across to show what I mean (only the embedding part). If you are going to do it this way, you can use our main page www.brightkeyhomes.sg and/or a project page www.brightkeyhomes.sg/willowcrest-at-ambergate to display

Target Market(s)

Real Estate Agents, Investors, Developers, General public age 30 & above

Industry/Entity Type

Advertising

Colors
9ccb3b
00a98f
0592cd
3176b5
ffcf3e
5c5c5c

Requirements
Should not have
• I prefer not to use real people stock images unless you are very sure it will work out well.

```html
<!DOCTYPE html>
<html lang="en">
<head>
<meta charset="utf-8">
<title>Brightkeyhomes.sg – Chatterloop Cover and Profile Image</title>
<link href="https://fonts.googleapis.com/css2?family=PT+Sans+Narrow:wght@700&family=Open+Sans:wght@400;600&display=swap" rel="stylesheet">
<style>
  :root {
    --page-bg: #eceae6;
    --cover-green: #23805a;
    --cover-green-dark: #17613f;
    --cover-green-light: #3c9a6f;
    --brand-green: #3db44a;
    --leaf-green: #9ccb3b;
    --ink: #2b2b2b;
    --muted: #5c5c5c;
    --white: #ffffff;
    --bezel: #141414;
    --silver: #d7d9dc;
  }
  html, body {
    margin: 0;
    padding: 0;
    width: 1029px;
    height: 1200px;
    overflow: hidden;
    background: var(--page-bg);
  }
  .sheet {
    position: relative;
    width: 1029px;
    height: 1200px;
    font-family: "Open Sans", Arial, sans-serif;
  }

  /* ---------- Cover ---------- */
  .cover {
    position: absolute;
    left: 44px;
    top: 150px;
    width: 940px;
    height: 345px;
    overflow: hidden;
    background: var(--cover-green);
    box-shadow: 0 2px 8px rgba(0,0,0,.18);
  }
  .cover__backdrop {
    position: absolute;
    inset: 0;
    background:
      linear-gradient(180deg, rgba(60,154,111,.55) 0%, rgba(35,128,90,0) 45%),
      linear-gradient(90deg, var(--cover-green-light) 0%, var(--cover-green) 45%, var(--cover-green-dark) 100%);
  }
  .cover__band {
    position: absolute;
    left: 0;
    top: 62px;
    width: 500px;
    height: 38px;
    background: linear-gradient(90deg, rgba(255,255,255,.96) 0%, rgba(255,255,255,.92) 85%, rgba(255,255,255,.55) 100%);
  }
  .cover__headline {
    position: absolute;
    left: 22px;
    top: 64px;
    margin: 0;
    font-family: "PT Sans Narrow", "Arial Narrow", sans-serif;
    font-weight: 700;
    font-size: 26px;
    line-height: 34px;
    color: var(--ink);
    white-space: nowrap;
  }
  .cover__headline em {
    font-style: normal;
    color: var(--brand-green);
  }
  .cover__features {
    position: absolute;
    left: 72px;
    top: 106px;
    margin: 0;
    padding: 0;
    list-style: none;
    display: flex;
    gap: 12px;
    font-size: 17px;
    color: var(--white);
    white-space: nowrap;
  }
  .cover__features li::before {
    content: "•";
    margin-right: 5px;
  }

  /* laptop holding the portal page */
  .laptop {
    position: absolute;
    left: 530px;
    top: 15px;
    width: 440px;
    height: 320px;
  }
  .laptop__lid {
    position: absolute;
    left: 0;
    top: 0;
    width: 440px;
    height: 292px;
    background: var(--bezel);
    border-radius: 14px 14px 0 0;
  }
  .laptop__camera {
    position: absolute;
    left: 217px;
    top: 7px;
    width: 5px;
    height: 5px;
    border-radius: 50%;
    background: #333;
  }
  .laptop__screen {
    position: absolute;
    left: 17px;
    top: 18px;
    width: 423px;
    height: 268px;
    background: linear-gradient(180deg, #f6f6f4 0%, #f6f6f4 18%, #2f8a5c 19%, #2f8a5c 22%, #6e9a62 23%, #8fb46b 55%, #5d8a5a 75%, #f3f3f1 76%, #f3f3f1 100%);
  }
  .laptop__base {
    position: absolute;
    left: -10px;
    top: 292px;
    width: 460px;
    height: 14px;
    background: linear-gradient(180deg, #f1f2f4 0%, var(--silver) 60%, #9a9ca0 100%);
    border-radius: 0 0 40px 40px;
  }

  /* ---------- Profile image ---------- */
  .profile {
    position: absolute;
    left: 44px;
    top: 620px;
    width: 300px;
    height: 300px;
    background: var(--white);
    box-shadow: 0 2px 8px rgba(0,0,0,.18);
    display: flex;
    flex-direction: column;
    align-items: center;
    justify-content: center;
    gap: 18px;
  }
  .profile__mark {
    width: 70px;
    height: 70px;
    border-radius: 50%;
    background: var(--leaf-green);
  }
  .profile__name {
    font-family: "Open Sans", Arial, sans-serif;
    font-weight: 600;
    font-size: 26px;
    color: var(--brand-green);
  }

  /* ---------- Captions ---------- */
  .caption {
    position: absolute;
    margin: 0;
    font-family: "Open Sans", Arial, sans-serif;
    font-size: 22px;
    font-weight: 400;
    color: var(--ink);
    letter-spacing: .3px;
  }
  .caption--cover { left: 44px; top: 512px; width: 940px; text-align: center; }
  .caption--profile { left: 44px; top: 936px; width: 300px; text-align: center; }
</style>
</head>
<body>
<main class="sheet">

  <section class="cover" aria-label="Chatterloop cover image">
    <div class="cover__backdrop" role="img" aria-label="Blurred green-toned photo of a condominium street with trees"></div>
    <div class="cover__band"></div>
    <h1 class="cover__headline">Singapore Latest Property Launches <em>In One Portal</em></h1>
    <ul class="cover__features">
      <li>Latest Projects</li>
      <li>Updated Info</li>
      <li>Best Pricing</li>
    </ul>

    <div class="laptop">
      <div class="laptop__lid">
        <span class="laptop__camera"></span>
        <div class="laptop__screen" role="img" aria-label="Brightkeyhomes.sg portal home page showing a featured condominium project"></div>
      </div>
      <div class="laptop__base"></div>
    </div>
  </section>
  <p class="caption caption--cover">Chatterloop Cover</p>

  <section class="profile" aria-label="Profile image">
    <span class="profile__mark"></span>
    <span class="profile__name">Brightkeyhomes</span>
  </section>
  <p class="caption caption--profile">Profile Image</p>

</main>
</body>
</html>
```